Quiet Lanterns for the Restless Inner Mind

I would like a website designed that would be used to upload podcasts, videos and written material about mental health. Where people will be being as honest, open and truthful as they can about mental health issues.
I would like it to look calming and soothing. Inspired by Dorlac's paintings and colour schemes.

I am on Brightlane as Dr Helen Maddox - and chirpbox as drhelenmaddox

Target Market(s)

Healthcare professionals and users of services who want to think at a deeper level about the nature of mental illness

Number of Pages Required

1 page

```html
<!DOCTYPE html>
<html lang="en">
<head>
<meta charset="utf-8">
<title>Quiet Lanterns for the Restless Inner Mind</title>
<link rel="stylesheet" href="https://fonts.googleapis.com/css2?family=Raleway:wght@300;400;500;600&family=Montserrat:wght@400;500;600&display=swap">
<style>
:root{
  --paper:#eeebe6;
  --card:#f2efeb;
  --sage:#b8c5c3;
  --sage-card:#a9b5b0;
  --slate:#5e7572;
  --deep:#2f4a34;
  --footer:#4a5754;
  --ink:#4b5856;
  --muted:#8e9895;
  --teal:#4fd1c1;
  --line:#c9ccc8;
}
*{box-sizing:border-box;margin:0;padding:0}
html,body{width:1200px;height:3736px;overflow:hidden}
body{position:relative;background:var(--paper);font-family:"Montserrat",sans-serif;color:var(--ink)}
.abs{position:absolute}
.photo{position:absolute}
.header{position:absolute;left:0;top:0;width:1200px;height:90px;border-bottom:1px solid #d8d5d0}
.brand{position:absolute;display:flex;align-items:center;gap:8px;font-family:"Raleway",sans-serif;font-weight:600;font-size:15px;color:var(--deep)}
.brand .dot{width:14px;height:14px;border-radius:50%;background:var(--deep)}
.nav a{position:absolute;top:36px;font-size:14px;color:var(--ink);text-decoration:none;font-family:"Raleway",sans-serif;font-weight:500}
.hero-card{position:absolute;left:573px;top:151px;width:286px;height:382px;background:var(--sage-card);padding:62px 22px 0 23px;box-shadow:0 6px 18px rgba(0,0,0,.12)}
.hero-card h1{font-family:"Raleway",sans-serif;font-weight:300;font-size:36px;line-height:46px;color:#fff}
.hero-card p{margin-top:24px;font-size:11.5px;line-height:21px;color:#eef2f0}
.btn-dark{position:absolute;left:26px;bottom:24px;width:106px;height:35px;background:var(--deep);color:#fff;font-size:12px;display:flex;align-items:center;justify-content:center;gap:8px}
.band{position:absolute;left:0;width:1200px;background:var(--sage);overflow:hidden}
.band .circle{position:absolute;border-radius:50%;border:1px solid rgba(255,255,255,.18);background:rgba(255,255,255,.05)}
.sec-title{position:absolute;font-family:"Raleway",sans-serif;font-weight:300;font-size:38px;letter-spacing:12px;line-height:1}
.on-band{color:#fff}
.on-paper{color:#6c7b78}
.rule{position:absolute;height:1px}
.btn-light{position:absolute;background:var(--paper);color:#6c7b78;font-size:11.5px;display:flex;align-items:center;justify-content:center}
.btn-slate{position:absolute;background:var(--slate);color:#eef;font-size:11.5px;display:flex;align-items:center;justify-content:center}
.pod{position:absolute;top:887px;width:238px;height:342px;background:var(--card)}
.pod .art{height:223px;position:relative}
.pod .play{position:absolute;left:14px;top:16px}
.pod .meta{display:flex;justify-content:space-between;padding:8px 14px 0;font-size:10.5px;color:var(--muted)}
.pod p{padding:10px 14px 0;font-size:11.5px;line-height:19px;color:#3e4846}
.pod .more{padding:3px 14px 0;font-size:10px;color:#3e4846}
.pod.fade{opacity:.55}
.arrow{position:absolute;width:30px;height:30px;border-radius:50%;border:1.5px solid #fff;display:flex;align-items:center;justify-content:center}
.video-img{position:absolute;overflow:hidden}
.video-img .play-btn{position:absolute;left:50%;top:50%;width:66px;height:66px;margin:-33px 0 0 -33px;border-radius:50%;background:rgba(79,209,193,.85);display:flex;align-items:center;justify-content:center}
.vtext{position:absolute;width:260px}
.vtext h3{font-family:"Raleway",sans-serif;font-weight:500;font-size:28px;letter-spacing:2px;color:#5e7572}
.vtext p{margin-top:10px;font-size:11.5px;line-height:19px;color:#5a6462}
.vtext .learn{margin-top:10px;font-size:11.5px;font-weight:600;color:#4a5e5b}
.vtext .also{margin-top:22px;font-size:11.5px;color:var(--muted)}
.vtext .also b{color:#4a5e5b}
.art-card{position:absolute;background:var(--card);overflow:hidden}
.art-card h4{font-size:12px;font-weight:600;color:#4a5e5b;line-height:16px}
.art-card .date{font-size:8px;color:var(--muted);margin:3px 0 6px}
.art-card .body{font-size:9px;line-height:15px;color:#4a5453}
.readtag{position:absolute;font-size:8.5px;color:#fff}
.newsletter{position:absolute;left:0;top:2850px;width:1200px;height:229px;background:linear-gradient(180deg,#efe6e4 0%,#f4ebe3 55%,#e9d6c8 100%)}
.field{position:absolute;background:#f6f3ef;border:1px solid #e2ded8;font-size:11px;color:#b0b3b0;padding:8px 13px}
.footer{position:absolute;left:0;top:3523px;width:1200px;height:213px;background:var(--footer)}
.footer a{position:absolute;top:80px;color:#fff;font-size:14px;text-decoration:none;font-family:"Raleway",sans-serif;font-weight:500}
.social{position:absolute;top:77px;display:flex;align-items:center;gap:5px;font-size:11px;color:#c8d0ce}
.social i{width:10px;height:10px;border-radius:50%;background:#8d9a97;display:block}
</style>
</head>
<body>

<header class="header">
  <div class="brand" style="left:232px;top:32px"><span class="dot"></span>Quiet Lanterns</div>
  <nav class="nav">
    <a style="left:572px">Home</a>
    <a style="left:655px">Podcasts</a>
    <a style="left:758px">Blog</a>
    <a style="left:831px">About</a>
    <a style="left:915px">Contact</a>
  </nav>
</header>

<section class="hero">
  <div class="photo" role="img" aria-label="Two men in headphones talking at a podcast desk" style="left:0;top:128px;width:237px;height:464px;background:linear-gradient(135deg,#9db6c2,#b49078 60%,#6f5a4a)"></div>
  <div class="photo" role="img" aria-label="Smiling host speaking into a studio microphone" style="left:280px;top:91px;width:398px;height:536px;background:linear-gradient(160deg,#a89f98,#8a7465 55%,#d9d5d1)"></div>
  <div class="photo" role="img" aria-label="Host seated on a chair holding a microphone by a window" style="left:892px;top:129px;width:308px;height:463px;background:linear-gradient(150deg,#a7d6d2,#5a4a3a 55%,#c0873e)"></div>
  <div class="hero-card">
    <h1>Quiet<br>Lanterns</h1>
    <p>Elevating awareness around suicide, depression and mental wellness. Explore our podcasts and candid interviews with many individuals who share their experiences in an open and honest way.</p>
    <div class="btn-dark">Explore <svg width="7" height="10" viewBox="0 0 7 10"><path d="M1 1l4 4-4 4" stroke="#fff" fill="none" stroke-width="1.4"/></svg></div>
  </div>
</section>

<section class="band" style="top:730px;height:604px">
  <div class="circle" style="left:470px;top:-120px;width:300px;height:300px"></div>
  <div class="sec-title on-band" style="left:231px;top:42px">PODCASTS</div>
  <div class="rule" style="left:500px;top:61px;width:313px;background:#e8eeed"></div>
  <div class="btn-light" style="left:831px;top:45px;width:162px;height:33px">Browse All Podcasts</div>
  <p class="abs" style="left:231px;top:90px;width:300px;font-size:11.5px;line-height:19px;color:#fff">Explore our collection of podcasts on many topics about mental health, updated weekly.</p>
</section>

<div class="pod fade" style="left:-19px">
  <div class="art" role="img" aria-label="Podcast cover with a professor in a studio" style="background:linear-gradient(135deg,#6a7a85,#3c4650)"></div>
  <div class="meta"><span>Description</span><span>30 mins</span></div>
  <p>Prof. Evan Marsh talks about mental wellness at Brookfield prevention in this latest podcast</p>
  <div class="more">More ›</div>
</div>
<div class="pod" style="left:231px">
  <div class="art" role="img" aria-label="Podcast cover with two women recording in a studio" style="background:linear-gradient(135deg,#c6a27a,#8d7257)"></div>
  <div class="meta"><span>Description</span><span>45 mins</span></div>
  <p>Nora Vell shares her journey overcoming her mental issues and opens up in this latest pod…</p>
  <div class="more">More ›</div>
</div>
<div class="pod" style="left:480px">
  <div class="art" role="img" aria-label="Podcast cover with a host in headphones at a microphone" style="background:linear-gradient(135deg,#5f6f7c,#2e3944)"></div>
  <div class="meta"><span>Description</span><span>15 mins</span></div>
  <p>Dr. Owen sits down with our new guest Clara for our September podcast. Topic of the day…</p>
  <div class="more">More ›</div>
</div>
<div class="pod" style="left:730px">
  <div class="art" role="img" aria-label="Podcast cover with a woman speaking into a microphone" style="background:linear-gradient(135deg,#3f4f78,#1f2a4a)"></div>
  <div class="meta"><span>Description</span><span>35 mins</span></div>
  <p>Saturday Podcast with Ivy &amp; Dana focuses on the stigma surrounding suicide survivors…</p>
  <div class="more">More ›</div>
</div>
<div class="pod fade" style="left:980px">
  <div class="art" role="img" aria-label="Podcast cover with a guest in a bright studio" style="background:linear-gradient(135deg,#8aa1ad,#5b6c78)"></div>
  <div class="meta"><span>Description</span><span>40 mins</span></div>
  <p>Nora Vell shares her journey overcoming her mental issues and opens up in this latest pod</p>
  <div class="more">More ›</div>
</div>
<svg class="abs" style="left:0;top:887px" width="1200" height="40" aria-hidden="true">
  <g fill="none" stroke="var(--teal)" stroke-width="1.6">
    <circle cx="21" cy="27" r="10"/><circle cx="256" cy="27" r="10"/><circle cx="506" cy="27" r="10"/><circle cx="755" cy="27" r="10"/><circle cx="1004" cy="27" r="10"/>
  </g>
  <g fill="var(--teal)">
    <path d="M18 22l8 5-8 5z"/><path d="M253 22l8 5-8 5z"/><path d="M503 22l8 5-8 5z"/><path d="M752 22l8 5-8 5z"/><path d="M1001 22l8 5-8 5z"/>
  </g>
</svg>
<div class="arrow" style="left:555px;top:1262px"><svg width="8" height="12" viewBox="0 0 8 12"><path d="M6 1L1 6l5 5" stroke="#fff" fill="none" stroke-width="1.4"/></svg></div>
<div class="arrow" style="left:614px;top:1262px"><svg width="8" height="12" viewBox="0 0 8 12"><path d="M2 1l5 5-5 5" stroke="#fff" fill="none" stroke-width="1.4"/></svg></div>

<section class="videos">
  <div class="sec-title on-paper" style="left:231px;top:1443px">VIDEOS</div>
  <div class="rule" style="left:424px;top:1462px;width:374px;background:#9aa5a2"></div>
  <div class="btn-slate" style="left:824px;top:1445px;width:144px;height:34px">Browse All Videos</div>

  <div class="video-img" role="img" aria-label="Two people recording a podcast in a brick studio" style="left:268px;top:1535px;width:312px;height:170px;background:linear-gradient(135deg,#8d8a85,#6f7c86 50%,#b59a7c)"><div class="play-btn"><svg width="22" height="26" viewBox="0 0 22 26"><path d="M2 1l19 12L2 25z" fill="#2d3a3a"/></svg></div></div>
  <div class="vtext" style="left:630px;top:1556px">
    <h3>Owen Hartley</h3>
    <p>We sit down for a candid discussion with depression expert Dr. Owen Hartley who helps us shine a spotlight on the culture of…</p>
    <div class="learn">Learn More &gt;&gt;</div>
    <div class="also">Also Available As: <b>Podcast</b></div>
  </div>
  <div class="rule" style="left:231px;top:1748px;width:737px;background:var(--line)"></div>

  <div class="vtext" style="left:296px;top:1810px">
    <h3>Tom Aldery</h3>
    <p>Talk show host Tom Aldery shares his experience on alcoholism and suicide during his youth.</p>
    <div class="learn">Learn More &gt;&gt;</div>
  </div>
  <div class="video-img" role="img" aria-label="Talk show host seated at a desk by office windows" style="left:618px;top:1791px;width:314px;height:171px;background:linear-gradient(135deg,#a49477,#5a5a52 55%,#c4c0b6)"><div class="play-btn"><svg width="22" height="26" viewBox="0 0 22 26"><path d="M2 1l19 12L2 25z" fill="#2d3a3a"/></svg></div></div>
  <div class="rule" style="left:231px;top:2005px;width:737px;background:var(--line)"></div>

  <div class="video-img" role="img" aria-label="Two women in headphones laughing in a blue studio" style="left:268px;top:2047px;width:312px;height:170px;background:linear-gradient(135deg,#2f5c86,#bfc6cc 55%,#e7e2dd)"><div class="play-btn"><svg width="22" height="26" viewBox="0 0 22 26"><path d="M2 1l19 12L2 25z" fill="#2d3a3a"/></svg></div></div>
  <div class="vtext" style="left:630px;top:2067px">
    <h3>Ruth Calder</h3>
    <p>Today's Talk outtakes with Ivy reads out readers' comments and share their thoughts about cultural percpetion on suicide and…</p>
    <div class="learn">Learn More &gt;&gt;</div>
    <div class="also">Also Available As: <b>Podcast</b></div>
  </div>
  <div class="rule" style="left:231px;top:2261px;width:737px;background:var(--line)"></div>
</section>

<section class="band" style="top:2352px;height:498px">
  <div class="circle" style="left:-140px;top:120px;width:420px;height:420px"></div>
  <div class="circle" style="left:880px;top:-60px;width:360px;height:360px"></div>
  <div class="sec-title on-band" style="left:231px;top:80px">ARTICLES</div>
  <div class="rule" style="left:472px;top:97px;width:370px;background:#e8eeed"></div>
  <div class="btn-light" style="left:866px;top:80px;width:102px;height:33px">Visit Blog</div>
</section>

<div class="art-card" style="left:231px;top:2500px;width:335px;height:250px">
  <div role="img" aria-label="Two people in conversation in a bright white room" style="height:160px;background:linear-gradient(135deg,#e8e6e2,#cfcbc4 60%,#3a3a3a)"></div>
  <div class="abs" style="left:0;top:150px;width:335px;height:100px;background:rgba(94,117,114,.88);padding:14px 11px">
    <div style="position:absolute;left:11px;top:-14px;font-size:8.5px;color:#fff">5 min read</div>
    <h4 style="color:#fff">How Sharing Can Prevent Depression</h4>
    <div class="date" style="color:#dfe6e4">26 Aug 2023</div>
    <div class="body" style="color:#fff">Ipsum dolor sit amet, consectetur adipiscing elit, sed do eiusmod tempor incididunt ut labore et dolore magna</div>
  </div>
</div>
<div class="art-card" style="left:580px;top:2500px;width:388px;height:116px">
  <div role="img" aria-label="Woman holding a book in a soft-lit room" style="position:absolute;left:0;top:0;width:130px;height:116px;background:linear-gradient(135deg,#8fa9b3,#2f3e4a)"></div>
  <div class="readtag" style="left:8px;top:101px">3 min read</div>
  <div class="abs" style="left:148px;top:16px;width:225px">
    <h4>Best Podcasts for Spiritual Wellbeing</h4>
    <div class="date">16 Aug 2023</div>
    <div class="body">Con sectetur adi piscing elit, sed do eiu smod tempor incididunt ut labore et dolore magna aliqua. Quis ipsum sus pendisse ultrices gravida.</div>
  </div>
</div>
<div class="art-card" style="left:580px;top:2634px;width:388px;height:116px">
  <div role="img" aria-label="Woman with pink hair at a microphone" style="position:absolute;left:0;top:0;width:130px;height:116px;background:linear-gradient(135deg,#c8a6b5,#6b5a5e)"></div>
  <div class="readtag" style="left:8px;top:101px">12 min read</div>
  <div class="abs" style="left:148px;top:10px;width:225px">
    <h4>How To Overcome Depression and Thoughts of Suicide by Dr. Mei Lorne</h4>
    <div class="date">11 Aug 2023</div>
    <div class="body">Dolor sit amet, con sectetur adi piscing elit, sed do eiusmod tempor incididunt ut labore et…</div>
  </div>
</div>
<div class="arrow" style="left:531px;top:2785px"><svg width="8" height="12" viewBox="0 0 8 12"><path d="M6 1L1 6l5 5" stroke="#fff" fill="none" stroke-width="1.4"/></svg></div>
<div class="arrow" style="left:590px;top:2785px"><svg width="8" height="12" viewBox="0 0 8 12"><path d="M2 1l5 5-5 5" stroke="#fff" fill="none" stroke-width="1.4"/></svg></div>

<section class="newsletter">
  <div role="img" aria-label="Misty hillside with a figure celebrating at sunset" style="position:absolute;left:750px;top:40px;width:450px;height:189px;background:linear-gradient(160deg,rgba(233,214,200,0) 20%,#d9b59c 70%,#c99c82);clip-path:polygon(0 100%,40% 55%,70% 35%,100% 20%,100% 100%)"></div>
  <h2 class="abs" style="left:0;width:1200px;top:56px;text-align:center;font-family:'Raleway',sans-serif;font-weight:300;font-size:25px;letter-spacing:3.5px;color:#6c7b78">SUBSCRIBE TO OUR NEWSLETTER</h2>
  <p class="abs" style="left:0;width:1200px;top:100px;text-align:center;font-size:12px;color:#5a6462">Stay up to date with the best content and podcasts with our newsletter</p>
  <div class="abs" style="left:354px;top:136px;width:364px;height:34px;background:rgba(255,255,255,.55);font-size:12px;color:#fff;padding:9px 12px">Email</div>
  <div class="btn-slate" style="left:718px;top:136px;width:125px;height:34px;font-weight:600;font-size:12.5px;color:#fff">Subscribe</div>
</section>

<section class="contact">
  <div class="photo" role="img" aria-label="Stack of balanced pebbles on a beach by the sea" style="left:0;top:3079px;width:554px;height:444px;background:linear-gradient(180deg,#5d6a70 0%,#8a9397 45%,#b8ada2 75%,#8c7f74 100%)"></div>
  <h2 class="abs" style="left:599px;top:3150px;font-family:'Raleway',sans-serif;font-weight:300;font-size:25px;letter-spacing:3px;color:#6c7b78">CONTACT US</h2>
  <p class="abs" style="left:601px;top:3193px;width:350px;font-size:11.5px;line-height:17px;color:#5a6462">Questions or requests for our next podcasts? We'd love to hear from you. Why not drop us a line?</p>
  <div class="field" style="left:601px;top:3244px;width:294px;height:29px">Name</div>
  <div class="field" style="left:601px;top:3291px;width:294px;height:30px">Email address</div>
  <div class="field" style="left:601px;top:3336px;width:294px;height:96px">Type your message here</div>
  <div class="btn-slate" style="left:602px;top:3443px;width:99px;height:31px;font-weight:600;color:#fff">Send</div>
</section>

<footer class="footer">
  <div class="brand" style="left:232px;top:78px;color:#fff"><span class="dot" style="background:#fff"></span>Quiet Lanterns</div>
  <a style="left:400px">Home</a>
  <a style="left:484px">Podcasts</a>
  <a style="left:587px">Blog</a>
  <a style="left:660px">About</a>
  <a style="left:745px">Contact</a>
  <div class="social" style="left:800px"><i></i>Brightlane</div>
  <div class="social" style="left:870px"><i></i>Gathernest</div>
  <div class="social" style="left:942px"><i></i>Snapfold</div>
  <div class="rule" style="left:231px;top:184px;width:737px;background:#7c8a87"></div>
  <p class="abs" style="left:0;width:1200px;top:193px;text-align:center;font-size:10px;color:#c8d0ce">www.quietlanterns.example</p>
</footer>

</body>
</html>
```